Card Design for my dog training business Brightpaw Obedience

Need a business card design for my dog training business with my new logo. Want the card to come off professional yet fun. Want it to be very eye catchy as well. I normally have these at vet clinics, pet stores, and groomers. so need it to look better than my competitors.
Target Market(s)
dog owners
Industry/Entity Type
Dog Training
Contact Information for Business Card
needs logo, my name and info
Font styles to use
Serif
Colors
0255a3
ffffff
ec1f27
000000
333333
fbfbfb
Requirements
Must have
- Brightpaw Obedience
- Felix Orland
- 415 903 2276
- info@brightpawobedience.example
- www.brightpawobedience.example

```html
<!DOCTYPE html>
<html lang="en">
<head>
<meta charset="utf-8">
<title>Brightpaw Obedience – Business Card</title>
<link rel="stylesheet" href="https://fonts.googleapis.com/css2?family=EB+Garamond:ital,wght@0,500;1,400&family=Open+Sans:wght@400;700&display=swap">
<style>
  :root {
    --stage: #2b2b2b;
    --card-dark: #1c1a1b;
    --card-light: #ffffff;
    --ink: #000000;
    --ink-soft: #333333;
    --paper: #fbfbfb;
    --muted: #6b6b6b;
  }
  * { margin: 0; padding: 0; box-sizing: border-box; }
  html, body { width: 1200px; height: 892px; overflow: hidden; }
  body {
    background: var(--stage);
    position: relative;
    font-family: "Open Sans", Arial, sans-serif;
  }
  .card {
    position: absolute;
    width: 560px;
    height: 320px;
    border-radius: 2px;
    overflow: hidden;
    box-shadow: 0 10px 30px rgba(0,0,0,0.45);
  }

  /* Back side */
  .card-back {
    left: 90px;
    top: 90px;
    background: linear-gradient(160deg, #2a2829 0%, var(--card-dark) 60%);
  }
  .card-back .brand {
    position: absolute;
    left: 0; right: 0;
    top: 96px;
    text-align: center;
    font-family: "EB Garamond", Georgia, serif;
    font-weight: 500;
    font-size: 40px;
    letter-spacing: 1px;
    color: var(--paper);
  }
  .card-back .tagline {
    position: absolute;
    left: 0; right: 0;
    bottom: 52px;
    text-align: center;
    font-family: "EB Garamond", Georgia, serif;
    font-style: italic;
    font-size: 17px;
    color: #d8d8d8;
  }

  /* Front side */
  .card-front {
    left: 550px;
    top: 480px;
    background: var(--card-light);
  }
  .card-front .brand {
    position: absolute;
    right: 34px;
    top: 44px;
    display: flex;
    align-items: center;
    gap: 10px;
    font-family: "EB Garamond", Georgia, serif;
    font-weight: 500;
    font-size: 26px;
    color: var(--ink);
  }
  .card-front .brand-dot {
    width: 12px; height: 12px;
    border-radius: 50%;
    background: var(--ink);
  }
  .contact {
    position: absolute;
    left: 36px;
    bottom: 86px;
  }
  .contact .person {
    font-weight: 700;
    font-size: 22px;
    color: var(--ink);
    margin-bottom: 10px;
  }
  .contact .line {
    font-size: 14px;
    color: var(--muted);
    line-height: 1.45;
  }
  .contact .label {
    font-weight: 700;
    color: var(--ink-soft);
  }
  .footer-band {
    position: absolute;
    left: 0; right: 0; bottom: 0;
    height: 190px;
    background: var(--ink);
    clip-path: polygon(0 100%, 0 77%, 86% 77%, 93% 0, 100% 0, 100% 100%);
  }
  .website {
    position: absolute;
    left: 36px;
    bottom: 12px;
    font-size: 15px;
    letter-spacing: 3px;
    color: var(--paper);
  }
</style>
</head>
<body>

  <section class="card card-back" aria-label="Card back">
    <div class="brand">Brightpaw Obedience</div>
    <p class="tagline">“Good manners start with one good walk a day.”</p>
  </section>

  <section class="card card-front" aria-label="Card front">
    <div class="brand"><span class="brand-dot"></span>Brightpaw Obedience</div>
    <div class="footer-band"></div>
    <div class="contact">
      <p class="person">Felix Orland</p>
      <p class="line"><span class="label">P:</span> 415 903 2276</p>
      <p class="line"><span class="label">E:</span> info@brightpawobedience.example</p>
    </div>
    <p class="website">www.brightpawobedience.example</p>
  </section>

</body>
</html>
```